Chimney Service company needs new business card design

We need a updated business card with our new logo added. We provide a full range of chimney services throughout Vermont and New Hampshire. The business card will be one sided and color. Attached is our current business card another document showing all the information we would like on the card.
We dont like a lot of flashy colors.... here is a link to our website to get an idea of our branding www.flueguardianvt.example

Target Market(s)

homeowners

Industry/Entity Type

Business

Contact Information for Business Card

See attached sheet for content.

Font styles to use
Serif
Sans Serif

Requirements
Must have
• all information provided on separate sheet
Should not have
• Additional information that may clogg up design

```html
<!DOCTYPE html>
<html lang="en">
<head>
<meta charset="utf-8">
<title>Flue Guardian Business Card</title>
<link rel="stylesheet" href="https://fonts.googleapis.com/css2?family=Cinzel:wght@400;700&family=Lato:wght@400&display=swap">
<style>
  :root {
    --page-bg: #e8e3dc;
    --card-dark: #111112;
    --card-mid: #1d1d1f;
    --accent-red: #a3161b;
    --accent-red-light: #c0262b;
    --text-light: #ece7e2;
    --text-muted: #d6d0ca;
    --emblem-silver: #d9d5d0;
  }
  html, body {
    margin: 0;
    padding: 0;
    width: 1200px;
    height: 1047px;
    overflow: hidden;
    background: var(--page-bg);
  }
  .business-card {
    position: absolute;
    left: 60px;
    top: 230px;
    width: 1080px;
    height: 588px;
    border-radius: 26px;
    overflow: hidden;
    background: linear-gradient(160deg, var(--card-mid) 0%, var(--card-dark) 55%, #0b0b0c 100%);
    box-shadow: 0 10px 30px rgba(0,0,0,0.25);
  }
  .brand-block {
    position: absolute;
    left: 60px;
    width: 440px;
    top: 126px;
    text-align: center;
  }
  .brand-square {
    display: block;
    width: 164px;
    height: 164px;
    margin: 0 auto;
    box-sizing: border-box;
    border: 12px solid var(--emblem-silver);
  }
  .brand-name {
    margin: 42px 0 0;
    font-family: "Cinzel", serif;
    font-weight: 400;
    font-size: 42px;
    letter-spacing: 1px;
    color: var(--emblem-silver);
    white-space: nowrap;
  }
  .divider {
    position: absolute;
    left: 555px;
    top: 93px;
    width: 3px;
    height: 320px;
    background: var(--accent-red);
  }
  .contact-list {
    position: absolute;
    left: 611px;
    top: 92px;
    margin: 0;
    padding: 0;
    list-style: none;
    font-family: "Lato", sans-serif;
    font-size: 22px;
    color: var(--text-light);
    letter-spacing: 0.5px;
  }
  .contact-list li {
    display: flex;
    align-items: center;
    height: 33px;
  }
  .contact-icon {
    width: 18px;
    height: 18px;
    margin-right: 16px;
    fill: var(--accent-red-light);
  }
  .services {
    position: absolute;
    left: 611px;
    top: 214px;
  }
  .services-title {
    margin: 0 0 6px;
    font-family: "Cinzel", serif;
    font-weight: 700;
    font-size: 29px;
    color: var(--accent-red);
    letter-spacing: 0.5px;
  }
  .services-list {
    margin: 0;
    padding: 0;
    list-style: none;
    font-family: "Lato", sans-serif;
    font-size: 23px;
    line-height: 33px;
    color: var(--text-light);
  }
  .service-area {
    position: absolute;
    left: 0;
    right: 0;
    top: 474px;
    text-align: center;
    font-family: "Cinzel", serif;
    font-size: 23px;
    color: var(--text-muted);
    letter-spacing: 0.5px;
  }
  .service-area em {
    font-family: "Lato", sans-serif;
    font-style: italic;
    text-transform: none;
  }
  .assurance-band {
    position: absolute;
    left: 0;
    right: 0;
    bottom: 0;
    height: 66px;
    background: linear-gradient(180deg, var(--accent-red-light) 0%, var(--accent-red) 60%, #7e1014 100%);
    display: flex;
    align-items: center;
    justify-content: center;
    font-family: "Cinzel", serif;
    font-size: 25px;
    color: var(--text-muted);
    letter-spacing: 0.5px;
    white-space: nowrap;
  }
</style>
</head>
<body>
  <div class="business-card">
    <div class="brand-block">
      <span class="brand-square"></span>
      <p class="brand-name">FLUE GUARDIAN</p>
    </div>

    <div class="divider"></div>

    <ul class="contact-list">
      <li>
        <svg class="contact-icon" viewBox="0 0 24 24" aria-hidden="true"><path d="M6.6 10.8a15.1 15.1 0 0 0 6.6 6.6l2.2-2.2a1 1 0 0 1 1-.25 11.4 11.4 0 0 0 3.6.57 1 1 0 0 1 1 1V20a1 1 0 0 1-1 1A17 17 0 0 1 3 4a1 1 0 0 1 1-1h3.5a1 1 0 0 1 1 1c0 1.25.2 2.45.57 3.57a1 1 0 0 1-.25 1z"/></svg>
        802-555-0147
      </li>
      <li>
        <svg class="contact-icon" viewBox="0 0 24 24" aria-hidden="true"><path d="M2 5h20v14H2z M2 5l10 7 10-7" fill="var(--accent-red-light)"/><path d="M3 6l9 6.3L21 6" fill="none" stroke="var(--card-dark)" stroke-width="1.6"/></svg>
        info@flueguardianvt.example
      </li>
      <li>
        <svg class="contact-icon" viewBox="0 0 24 24" aria-hidden="true"><circle cx="12" cy="12" r="10"/><g fill="none" stroke="var(--card-dark)" stroke-width="1.4"><ellipse cx="12" cy="12" rx="4" ry="10"/><path d="M2 12h20M4 7h16M4 17h16"/></g></svg>
        www.flueguardianvt.example
      </li>
    </ul>

    <div class="services">
      <h2 class="services-title">SERVICES WE PROVIDE</h2>
      <ul class="services-list">
        <li>Full Masonry Services</li>
        <li>Historic chimney restoration</li>
        <li>Stainless steel liners</li>
        <li>New Chimney installations</li>
        <li>NFSA Certified Chimney sweeps</li>
      </ul>
    </div>

    <p class="service-area">SERVING VT AND NEW HAMPSHIRE-<em>since 1989</em></p>

    <div class="assurance-band">Fully Insured–Free Estimates | Family owned and operated</div>
  </div>
</body>
</html>
```